MRT Property - Business Cards

Looking for a business card & general letterhead, signage etc design for our new logo.

Colours:
000a20
0056a2
00b5ef
0088ce
68cef2

Fonts:
Poppins
Karla

Please keep look and feel of new brand - example in the zip package I sent.

```html
<!DOCTYPE html>
<html lang="en">
<head>
<meta charset="utf-8">
<title>MRT Property – Business Cards</title>
<link href="https://fonts.googleapis.com/css2?family=Poppins:wght@300;400;500;600;700&display=swap" rel="stylesheet">
<style>
  :root{
    --stage:#222224;
    --navy:#000a20;
    --card-navy:#0f1429;
    --blue-deep:#0056a2;
    --blue-mid:#0088ce;
    --blue-bright:#00b5ef;
    --blue-light:#68cef2;
    --white:#ffffff;
  }
  *{box-sizing:border-box;margin:0;padding:0}
  html,body{width:1200px;height:711px;overflow:hidden;background:var(--stage)}
  body{font-family:"Poppins",sans-serif;position:relative}
  .card{
    position:absolute;width:540px;height:309px;border-radius:22px;
    background:var(--card-navy);overflow:hidden;
    box-shadow:0 0 0 3px var(--blue-light),0 18px 40px rgba(0,0,0,.55);
  }
  .card--back{left:36px;top:201px}
  .card--front{left:624px;top:201px}

  /* back */
  .back-pattern{position:absolute;inset:0;
    background:linear-gradient(160deg,#17307a 0%,#141e4d 45%,#0f1429 100%)}
  .back-brand{position:absolute;right:34px;bottom:34px;
    font-weight:600;font-size:15px;color:var(--blue-mid);letter-spacing:.2px}

  /* front */
  .front-art{position:absolute;inset:0}
  .front-brand{position:absolute;left:30px;top:30px;
    font-weight:700;font-size:30px;line-height:1;color:var(--blue-deep)}
  .person{position:absolute;right:30px;top:22px;text-align:right}
  .person__name{font-size:24px;line-height:1.1;color:var(--blue-light);font-weight:400}
  .person__name b{font-weight:700;color:var(--blue-deep)}
  .person__role{font-size:11px;color:var(--white);font-weight:500}
  .accent-bar{position:absolute;right:0;top:20px;width:14px;height:42px;background:var(--blue-deep)}
  .address{position:absolute;left:30px;top:112px;font-size:11.5px;line-height:1.45;color:var(--white)}
  .contact{position:absolute;left:30px;top:178px;list-style:none;font-size:11.5px;color:var(--white)}
  .contact li{display:flex;align-items:center;gap:8px;height:19px}
  .contact svg{width:12px;height:12px;flex:none}
</style>
</head>
<body>

<section class="card card--back" aria-label="Business card back">
  <div class="back-pattern" role="img" aria-label="Repeating brand mark pattern in shades of navy and blue"></div>
  <div class="back-brand">MRT Property</div>
</section>

<section class="card card--front" aria-label="Business card front">
  <svg class="front-art" viewBox="0 0 540 309" aria-hidden="true">
    <path d="M150 309 C300 270 360 170 420 120 C460 92 500 82 540 78 L540 309 Z" fill="var(--blue-deep)"/>
    <path d="M0 250 C110 280 230 285 340 225 C250 282 120 292 0 268 Z" fill="var(--blue-light)"/>
    <path d="M0 268 C120 292 250 282 340 225 C270 285 150 300 60 309 L0 309 Z" fill="var(--navy)" opacity=".6"/>
  </svg>

  <div class="front-brand">MRT Property</div>

  <div class="accent-bar"></div>
  <div class="person">
    <p class="person__name"><b>Liam</b> Carver</p>
    <p class="person__role">Director</p>
  </div>

  <p class="address">Suite 4.12, Block 3<br>18 Harbourline Road<br>Riverside Park NSW 2190</p>

  <ul class="contact">
    <li>
      <svg viewBox="0 0 24 24"><path fill="#68cef2" d="M6.6 10.8a15 15 0 0 0 6.6 6.6l2.2-2.2a1 1 0 0 1 1-.25 11.4 11.4 0 0 0 3.6.57 1 1 0 0 1 1 1V20a1 1 0 0 1-1 1A17 17 0 0 1 3 4a1 1 0 0 1 1-1h3.5a1 1 0 0 1 1 1c0 1.25.2 2.45.57 3.57a1 1 0 0 1-.25 1z"/></svg>
      +61 2 5550 0142
    </li>
    <li>
      <svg viewBox="0 0 24 24"><circle cx="12" cy="12" r="10" fill="none" stroke="#68cef2" stroke-width="2"/><path d="M2 12h20M12 2c3 3 3 17 0 20M12 2c-3 3-3 17 0 20" fill="none" stroke="#68cef2" stroke-width="1.6"/></svg>
      www.mrtproperty.com.au
    </li>
    <li>
      <svg viewBox="0 0 24 24"><rect x="2" y="5" width="20" height="14" rx="2" fill="none" stroke="#68cef2" stroke-width="2"/><path d="M3 6l9 7 9-7" fill="none" stroke="#68cef2" stroke-width="2"/></svg>
      info@mrtproperty.com.au
    </li>
  </ul>
</section>

</body>
</html>
```